Single Page Timetracking Dashboard Desktop App UI Design (Figma Link required)

Main Idea: a SaaS tool where employees can add their time and project in a playful way. There is a infographics and a list with tasks as well.

Based on the attached concept.png the brief is following:

- check the attached rough scribble
- add own ideas or change things if they add value
- Style: colourful, nerdy, professional saas, modern, beautiful, white space
- Quality expectation: inspiration1+2.png
- I will need a Figma link
- desktop only
- make something fresh and unique

Process:
I need to include 2-3 feedback rounds that will span probably around 7 days

Target Market(s)

Internal Business Tool for a Software Development Company

Industry/Entity Type

IT

Font styles to use
Other font styles liked:
• Could be monospace, not a must though

Requirements
Must have
• At least one page; Figma Link to the design;
Nice to have
• Microinterations like drop-down, hover/active colors; functionality specifications
Should not have
• Mobile view

```html
<!DOCTYPE html>
<html lang="en">
<head>
<meta charset="utf-8">
<title>Saas – Time Tracking Dashboard</title>
<link href="https://fonts.googleapis.com/css2?family=Ubuntu:wght@400;500;700&display=swap" rel="stylesheet">
<style>
  :root{
    --page:#ffffff;
    --brand:#ff8585;
    --brand-strong:#ff5c63;
    --active:#ff8080;
    --card:#ffffff;
    --chip:#e6e6e6;
    --ink:#111111;
    --muted:#555555;
    --task-bg:#fde0e2;
    --green:#62a600;
    --orange:#ea6500;
    --blue:#4164b9;
    --nav-grey:#d9d9d9;
  }
  *{box-sizing:border-box;margin:0;padding:0}
  html,body{width:1013px;height:1200px;overflow:hidden;background:var(--page)}
  body{position:relative;font-family:'Ubuntu',sans-serif;color:var(--ink)}
  .abs{position:absolute}
  .app{left:46px;top:42px;width:920px;height:1103px;background:var(--brand);border-radius:6px}
  .brand{left:63px;top:52px;font-size:29px;color:#fff;line-height:1}
  .nav-item{left:62px;width:59px;height:55px;color:#fff;font-size:14px;text-align:center;border-radius:6px;display:flex;flex-direction:column;align-items:center;justify-content:center;gap:5px}
  .nav-item.is-active{background:var(--brand-strong)}
  .nav-item svg{width:16px;height:16px}
  .card{left:140px;width:807px;background:var(--card);border-radius:6px}
  .card-title{font-size:17px;font-weight:500;line-height:1}
  /* calendar */
  .calendar{left:164px;top:129px;width:213px;height:154px;border:1px solid #222;border-radius:6px;background:#fff}
  .calendar-month{right:8px;top:10px;font-size:11px;font-weight:500}
  .calendar-month span{color:#bbb;font-weight:400}
  .calendar-days{left:5px;top:30px;width:202px;display:grid;grid-template-columns:repeat(7,1fr);font-size:3px;text-align:center;color:#444;letter-spacing:.1px}
  .calendar-days .weekend{color:var(--brand-strong)}
  .calendar-grid{left:5px;top:36px;width:202px;display:grid;grid-template-columns:repeat(7,1fr);grid-auto-rows:21.6px;border-top:1px solid #ddd;border-left:1px solid #ddd}
  .calendar-grid div{border-right:1px solid #ddd;border-bottom:1px solid #ddd;font-size:5px;text-align:right;padding:2px 3px;color:#333;background:linear-gradient(#fff,#f5f5f5)}
  .calendar-grid .weekend{color:var(--brand-strong)}
  .calendar-grid .outside{color:#ccc}
  .calendar-grid .is-selected{background:var(--brand-strong);color:#fff}
  /* selects */
  .select{left:393px;width:169px;height:28px;background:var(--chip);border-radius:4px;font-size:12.5px;font-weight:500;display:flex;align-items:center;justify-content:space-between;padding:0 9px}
  .select svg{width:8px;height:6px}
  .option{left:402px;font-size:9.5px;color:var(--muted);line-height:13.5px;width:160px}
  .note{left:163px;top:308px;width:399px;height:97px;background:var(--chip);border-radius:5px;padding:10px 11px;font-size:12.5px}
  /* duration chips */
  .chip{width:77px;height:29px;background:var(--chip);border-radius:5px;font-size:10px;font-weight:700;display:flex;align-items:center;justify-content:center}
  .chip.is-active{background:var(--active)}
  .duration{left:596px;top:285px;width:328px;text-align:center;font-size:43px;font-weight:700;line-height:1}
  .save{left:619px;top:360px;width:284px;height:44px;background:var(--brand-strong);border-radius:4px;color:#fff;font-size:20px;font-weight:700;display:flex;align-items:center;justify-content:center}
  /* pager */
  .pager{width:17px;height:17px;border-radius:50%;background:var(--nav-grey);display:flex;align-items:center;justify-content:center;font-size:9px;line-height:1}
  .pager.is-active{background:var(--active)}
  /* stats */
  .stat-heading{font-size:16px;line-height:1}
  .stat-total{font-size:16px;font-weight:700;line-height:1;text-align:right}
  .legend{font-size:13px;line-height:26px;text-align:right;white-space:pre}
  .divider{left:541px;top:532px;width:1px;height:192px;background:var(--active)}
  .pie{width:150px;height:150px}
  /* tasks */
  .tab{top:858px;font-size:17px;font-weight:500;line-height:1}
  .tab.is-active{color:var(--brand-strong)}
  .task{left:169px;top:917px;width:747px;height:131px;background:var(--task-bg);border-radius:5px}
  .task-type{left:14px;top:12px;font-size:18px;font-weight:700;line-height:1}
  .task-actions{right:16px;top:13px;font-size:14px;display:flex;gap:14px;align-items:center}
  .task-actions span{display:flex;gap:4px;align-items:center}
  .task-actions svg{width:12px;height:12px}
  .task-rule{left:0;top:39px;width:747px;height:1px;background:#222}
  .task-project{left:14px;top:54px;font-size:21px;font-weight:700;line-height:1}
  .task-time{right:18px;top:55px;font-size:16px;font-weight:700;line-height:1}
  .task-desc{left:14px;top:90px;font-size:13.5px;line-height:1}
  .task-date{right:18px;top:90px;font-size:16px;font-weight:700;line-height:1}
</style>
</head>
<body>
  <div class="abs app"></div>
  <div class="abs brand">Saas</div>

  <nav>
    <div class="abs nav-item is-active" style="top:114px">
      <svg viewBox="0 0 16 16" fill="none" stroke="#fff" stroke-width="1.8"><circle cx="8" cy="8" r="6.5"/><path d="M8 4.5V8h2.5"/></svg>
      <span>Clock</span>
    </div>
    <div class="abs nav-item" style="top:176px">
      <svg viewBox="0 0 16 16" fill="#fff"><rect x="1" y="2" width="1.4" height="13"/><rect x="1" y="13.6" width="14" height="1.4"/><rect x="4" y="8" width="2" height="5"/><rect x="7" y="5" width="2" height="8"/><rect x="10" y="9" width="2" height="4"/><rect x="13" y="4" width="2" height="9"/></svg>
      <span>Statistics</span>
    </div>
    <div class="abs nav-item" style="top:241px">
      <svg viewBox="0 0 16 16" fill="#fff"><rect x="0" y="1" width="4.5" height="4"/><rect x="5.7" y="1" width="4.5" height="4"/><rect x="11.4" y="1" width="4.5" height="4"/><rect x="0" y="6" width="4.5" height="4"/><rect x="5.7" y="6" width="4.5" height="4"/><rect x="11.4" y="6" width="4.5" height="4"/><rect x="0" y="11" width="4.5" height="4"/><rect x="5.7" y="11" width="4.5" height="4"/><rect x="11.4" y="11" width="4.5" height="4"/></svg>
      <span>Task</span>
    </div>
    <div class="abs nav-item" style="top:305px">
      <svg viewBox="0 0 16 16" fill="#fff"><circle cx="8" cy="4.5" r="3.5"/><path d="M1.5 16c0-4 3-6.5 6.5-6.5s6.5 2.5 6.5 6.5z"/></svg>
      <span>User</span>
    </div>
  </nav>

  <!-- Track your time -->
  <section class="abs card" style="top:72px;height:366px"></section>
  <h2 class="abs card-title" style="left:163px;top:93px">Track Your Time</h2>

  <div class="abs calendar">
    <div class="abs calendar-month">October <span>2023</span></div>
    <div class="abs calendar-days">
      <span class="weekend">SUNDAY</span><span>MONDAY</span><span>TUESDAY</span><span>WEDNESDAY</span><span>THURSDAY</span><span>FRIDAY</span><span class="weekend">SATURDAY</span>
    </div>
    <div class="abs calendar-grid">
      <div class="weekend">1</div><div>2</div><div>3</div><div>4</div><div>5</div><div>6</div><div class="weekend">7</div>
      <div class="weekend">8</div><div class="is-selected">9</div><div>10</div><div>11</div><div>12</div><div>13</div><div class="weekend">14</div>
      <div class="weekend">15</div><div>16</div><div>17</div><div>18</div><div>19</div><div>20</div><div class="weekend">21</div>
      <div class="weekend">22</div><div>23</div><div>24</div><div>25</div><div>26</div><div>27</div><div class="weekend">28</div>
      <div class="weekend">29</div><div>30</div><div>31</div><div class="outside">1</div><div class="outside">2</div><div class="outside">3</div><div class="outside">4</div>
    </div>
  </div>

  <div class="abs select" style="top:130px">Select Project
    <svg viewBox="0 0 8 6" fill="none" stroke="#222" stroke-width="1.2"><path d="M1 1.5l3 3 3-3"/></svg></div>
  <div class="abs select" style="top:166px">Select Type
    <svg viewBox="0 0 8 6" fill="none" stroke="#222" stroke-width="1.2"><path d="M1 1.5l3 3 3-3"/></svg></div>
  <div class="abs option" style="top:204px">Customer 1 Project 1</div>
  <div class="abs option" style="top:225px">Customer 2 Project 2</div>
  <div class="abs option" style="top:246px">Customer 1 Project 2</div>
  <div class="abs option" style="top:268px">Customer With Long Name and Project Name</div>

  <div class="abs note">What did you do?</div>

  <div class="abs chip" style="left:596px;top:129px">1h</div>
  <div class="abs chip is-active" style="left:683px;top:129px">2h</div>
  <div class="abs chip" style="left:764px;top:129px">3h</div>
  <div class="abs chip" style="left:847px;top:129px">4h</div>
  <div class="abs chip" style="left:596px;top:165px">5h</div>
  <div class="abs chip" style="left:683px;top:165px">6h</div>
  <div class="abs chip" style="left:764px;top:165px">7h</div>
  <div class="abs chip" style="left:847px;top:165px">8h</div>
  <div class="abs chip" style="left:596px;top:224px">0m</div>
  <div class="abs chip" style="left:683px;top:224px">15m</div>
  <div class="abs chip is-active" style="left:764px;top:224px">30m</div>
  <div class="abs chip" style="left:847px;top:224px">45m</div>

  <div class="abs duration">2h:30m</div>
  <div class="abs save">Save</div>

  <!-- Statistics -->
  <section class="abs card" style="top:468px;height:286px"></section>
  <h2 class="abs card-title" style="left:163px;top:490px">Statistice</h2>
  <div class="abs pager is-active" style="left:878px;top:489px">«</div>
  <div class="abs pager" style="left:902px;top:489px">»</div>

  <div class="abs stat-heading" style="left:163px;top:537px">Current Month</div>
  <div class="abs stat-total" style="right:497px;top:537px">Total: 50:45h</div>
  <svg class="abs pie" style="left:160px;top:570px" viewBox="-5 -10 150 150" role="img" aria-label="Pie chart of current month hours by customer">
    <path d="M70 70L101.9 130A68 68 0 1 1 70 2Z" fill="var(--blue)"/>
    <path transform="translate(4,-6)" d="M70 70L70 2A68 68 0 0 1 123.6 28.1Z" fill="var(--green)"/>
    <path transform="translate(6,3)" d="M70 70L127.7 34A68 68 0 0 1 106 127.7Z" fill="var(--orange)"/>
  </svg>
  <div class="abs legend" style="right:497px;top:666px">40:45h  Customer A  (89%)
10:00h  Customer B  (11%)</div>

  <div class="abs divider"></div>

  <div class="abs stat-heading" style="left:561px;top:537px">September</div>
  <div class="abs stat-total" style="right:89px;top:537px">Gesamt: 114:00h</div>
  <svg class="abs pie" style="left:558px;top:570px" viewBox="-5 -10 150 150" role="img" aria-label="Pie chart of September hours by customer">
    <path d="M70 70L101.9 130A68 68 0 1 1 70 2Z" fill="var(--blue)"/>
    <path transform="translate(4,-6)" d="M70 70L70 2A68 68 0 0 1 123.6 28.1Z" fill="var(--green)"/>
    <path transform="translate(6,3)" d="M70 70L127.7 34A68 68 0 0 1 106 127.7Z" fill="var(--orange)"/>
  </svg>
  <div class="abs legend" style="right:89px;top:587px">40:45h  Customer A  (53%)
08:10h  Customer B  (13%)
20:00h  Customer B  (34%)
22:45h  Customer B  (53%)
02:15h  Customer B  (13%)</div>

  <!-- Tasks -->
  <section class="abs card" style="top:795px;height:286px"></section>
  <h2 class="abs card-title" style="left:163px;top:816px">Your Tasks</h2>
  <div class="abs pager is-active" style="left:874px;top:815px">«</div>
  <div class="abs pager" style="left:898px;top:815px">»</div>

  <div class="abs tab is-active" style="left:169px">Wendnesday</div>
  <div class="abs tab" style="left:305px">Tuesday</div>
  <div class="abs tab" style="left:404px">Monday</div>
  <div class="abs tab" style="right:95px;font-weight:700">7h 30m</div>

  <article class="abs task">
    <div class="abs task-type">Coding</div>
    <div class="abs task-actions">
      <span><svg viewBox="0 0 12 12" fill="none" stroke="#111" stroke-width="1"><path d="M1.5 3h9M4.5 3V1.5h3V3M2.5 3l.7 8h5.6l.7-8M5 5v4.5M7 5v4.5"/></svg>Delete</span>
      <span><svg viewBox="0 0 12 12" fill="#111"><path d="M8.5 1l2.5 2.5-6.5 6.5H2V7.5z"/><path d="M1 11h2L1 9z"/></svg>Edit</span>
    </div>
    <div class="abs task-rule"></div>
    <div class="abs task-project">Customer A Project 1</div>
    <div class="abs task-time">4h 30m</div>
    <div class="abs task-desc">Some Description What The User did On That Project</div>
    <div class="abs task-date">December 9th</div>
  </article>
</body>
</html>
```